Looking for someone to design a business card for my plumbing business Quandor Plumbing Solutions I want the background also to be black, must attract clients. If possible I want the front to be the logo and the back to show maybe the details.

Target Market(s)

Clients

Industry/Entity Type

Plumbing maintenance

Contact Information for Business Card

Name: Felix, Contact: 0461 539 207, Email: quandorplumbingsolutions@mailbrook.example, Licence number 728093K

Font styles to use
Other font styles liked:
• as per logo maybe?

Colors

Designer to choose colors to be used in the design.

Requirements
Nice to have
• stating the service I provide, emergency plumbing, plumbing maintenance, drainage maintenance, block sewer and stormwater, camera and locating.

```html
<!DOCTYPE html>
<html lang="en">
<head>
<meta charset="utf-8">
<title>Quandor Plumbing Solutions – Business Card</title>
<link href="https://fonts.googleapis.com/css2?family=Montserrat:wght@400;500;700;800&display=swap" rel="stylesheet">
<style>
  :root {
    --backdrop: #cfcfcd;
    --card: #1f1f20;
    --accent: #4a90d4;
    --ink: #ffffff;
    --ink-soft: #e6e6e6;
  }
  * { box-sizing: border-box; margin: 0; padding: 0; }
  html, body { width: 1200px; height: 801px; overflow: hidden; }
  body {
    background: var(--backdrop);
    font-family: "Montserrat", sans-serif;
    display: flex;
    align-items: center;
    justify-content: center;
    gap: 40px;
  }
  .card {
    position: relative;
    width: 540px;
    height: 309px;
    background: var(--card);
    border-bottom: 5px solid var(--accent);
    border-left: 3px solid var(--accent);
    color: var(--ink);
    overflow: hidden;
  }

  /* Details side */
  .card-details { padding: 34px 36px 0 44px; }
  .card-details .tab {
    position: absolute;
    left: 0; top: 40px;
    width: 18px; height: 26px;
    background: var(--accent);
  }
  .person-name {
    font-weight: 700;
    font-size: 24px;
    letter-spacing: 0.5px;
    color: var(--accent);
    line-height: 1;
  }
  .person-role {
    font-size: 13px;
    color: var(--ink-soft);
    margin-top: 3px;
  }
  .licence {
    font-size: 13px;
    margin-top: 22px;
  }
  .contact-list { list-style: none; margin-top: 8px; }
  .contact-list li {
    display: flex;
    align-items: center;
    gap: 8px;
    font-size: 13px;
    line-height: 22px;
  }
  .contact-list svg { width: 12px; height: 12px; flex: none; }
  .services {
    list-style: none;
    margin-top: 20px;
    display: grid;
    grid-template-columns: auto auto;
    column-gap: 18px;
    row-gap: 5px;
    justify-content: start;
  }
  .services li {
    font-size: 13px;
    display: flex;
    align-items: center;
    gap: 8px;
  }
  .services li::before {
    content: "";
    width: 5px; height: 5px;
    border-radius: 50%;
    background: var(--accent);
  }

  /* Logo side */
  .card-brand {
    display: flex;
    align-items: center;
    justify-content: center;
    gap: 16px;
  }
  .brand-dot {
    width: 40px; height: 40px;
    border-radius: 50%;
    background: var(--accent);
    flex: none;
  }
  .brand-name {
    font-weight: 800;
    font-size: 27px;
    line-height: 1.1;
    letter-spacing: 1px;
    color: var(--ink);
    text-transform: uppercase;
  }
</style>
</head>
<body>

  <section class="card card-details">
    <span class="tab"></span>
    <h1 class="person-name">FELIX</h1>
    <p class="person-role">Founder &amp; CEO</p>
    <p class="licence">Licence number 728093K</p>
    <ul class="contact-list">
      <li>
        <svg viewBox="0 0 12 12" aria-hidden="true"><path d="M2.5 1 4.5 3.3 3.6 4.6a6 6 0 0 0 3.8 3.8l1.3-.9L11 9.5 9.8 11C5 10.6 1.4 7 1 2.2Z" fill="var(--accent)"/></svg>
        0461 539 207
      </li>
      <li>
        <svg viewBox="0 0 12 12" aria-hidden="true"><rect x="0.5" y="2" width="11" height="8" fill="var(--accent)"/><path d="M0.5 2 6 6.6 11.5 2" fill="none" stroke="var(--card)" stroke-width="1"/></svg>
        quandorplumbingsolutions@mailbrook.example
      </li>
      <li>
        <svg viewBox="0 0 12 12" aria-hidden="true"><circle cx="6" cy="6" r="5.5" fill="var(--accent)"/></svg>
        @QuandorPlumbingSolutions
      </li>
    </ul>
    <ul class="services">
      <li>Emergency plumbing</li>
      <li>Plumbing maintenance</li>
      <li>Drainage maintenance</li>
      <li>Camera and locating</li>
      <li>Block sewer and stormwater</li>
    </ul>
  </section>

  <section class="card card-brand">
    <span class="brand-dot"></span>
    <p class="brand-name">Quandor<br>Plumbing Solutions</p>
  </section>

</body>
</html>
```